Velmora Cabinets Letter Head and Email Signature

Hi
I would love a design package for a letterhead, email signature, even update my business card if you like if you can come up with a great idea for my new high end cabinet shop. Velmora Cabinets brings timeless craftsmanship to modern interiors, specializing in high end, custom cabinetry designed for architects and interior designers.

Target Market(s)

high end, luxury market

Industry/Entity Type

cabinet making

Requirements
Must have
• my colours of logo as the theme

```html
<!DOCTYPE html>
<html lang="en">
<head>
<meta charset="utf-8">
<title>Velmora Cabinets Business Card</title>
<link rel="stylesheet" href="https://fonts.googleapis.com/css2?family=Poppins:wght@400;500;600;700&family=Orbitron:wght@800&display=swap">
<style>
  :root {
    --green: #4a7b48;
    --green-deep: #3f6c3d;
    --black: #050505;
    --white: #ffffff;
    --stage-top: #ffffff;
    --stage-bottom: #575757;
    --ink: #1e1e1e;
  }
  * { margin: 0; padding: 0; box-sizing: border-box; }
  html, body { width: 1031px; height: 1200px; overflow: hidden; }
  body {
    position: relative;
    font-family: "Poppins", sans-serif;
    background: linear-gradient(to bottom, var(--stage-top) 0 593px, var(--stage-bottom) 593px 100%);
  }
  .card {
    position: absolute;
    left: 135px;
    width: 761px;
    height: 435px;
    overflow: hidden;
    box-shadow: 0 14px 18px rgba(0,0,0,0.28);
  }

  /* Brand lockup: plain square + name set in one colour and weight */
  .brand { position: absolute; display: flex; align-items: center; }
  .brand-square { flex: none; border-style: solid; border-color: var(--green); }
  .brand-name {
    color: var(--green);
    font-weight: 500;
    letter-spacing: 1px;
  }

  /* Front */
  .card-front { top: 89px; background: var(--black); }
  .card-front .brand { left: 157px; top: 134px; }
  .card-front .brand-square { width: 118px; height: 118px; border-width: 5px; margin-right: 40px; }
  .card-front .brand-name { font-size: 54px; line-height: 60px; }
  .web-band {
    position: absolute;
    left: 0; right: 0; top: 356px;
    height: 41px;
    background: var(--green);
    color: var(--white);
    text-align: center;
    font-size: 24px;
    line-height: 41px;
    letter-spacing: 4px;
  }
  .web-band strong { font-weight: 700; }

  /* Back */
  .card-back { top: 676px; background: linear-gradient(100deg, var(--white) 45%, #ececec); }
  .card-back .brand { left: 35px; top: 34px; }
  .card-back .brand-square { width: 84px; height: 84px; border-width: 4px; margin-right: 38px; }
  .card-back .brand-name { font-size: 38px; line-height: 42px; }
  .person { position: absolute; left: 34px; top: 166px; }
  .person-name {
    font-family: "Orbitron", sans-serif;
    font-weight: 800;
    font-size: 35px;
    color: var(--green);
    line-height: 1;
  }
  .person-title { margin-top: 9px; font-size: 17px; color: var(--ink); }
  .contact-band {
    position: absolute;
    left: 0; right: 0; top: 247px; bottom: 0;
    background: var(--black);
  }
  .green-panel { position: absolute; left: 0; top: 0; }
  .contacts {
    position: absolute;
    left: 34px; top: 275px;
    list-style: none;
    color: var(--white);
    font-size: 21px;
  }
  .contacts li { display: flex; align-items: center; height: 34px; }
  .contacts .icon {
    width: 22px; height: 22px;
    border-radius: 50%;
    background: var(--green);
    margin-right: 7px;
    flex: none;
    display: flex; align-items: center; justify-content: center;
  }
</style>
</head>
<body>
  <section class="card card-front">
    <div class="brand">
      <span class="brand-square"></span>
      <div class="brand-name">Velmora<br>Cabinets</div>
    </div>
    <div class="web-band">www.<strong>velmoracabinets</strong>.com</div>
  </section>

  <section class="card card-back">
    <div class="brand">
      <span class="brand-square"></span>
      <div class="brand-name">Velmora<br>Cabinets</div>
    </div>
    <div class="person">
      <div class="person-name">Dorian Keswick</div>
      <div class="person-title">Director Craftsman</div>
    </div>
    <div class="contact-band"></div>
    <svg class="green-panel" width="761" height="435" viewBox="0 0 761 435" role="img" aria-label="Large brand symbol area in green">
      <defs>
        <linearGradient id="panelTone" x1="0" y1="0" x2="1" y2="1">
          <stop offset="0" stop-color="var(--green)"/>
          <stop offset="1" stop-color="var(--green-deep)"/>
        </linearGradient>
      </defs>
      <polygon points="379,435 536,164 761,164 761,435" fill="url(#panelTone)"/>
      <line x1="372" y1="438" x2="531" y2="164" stroke="var(--white)" stroke-width="5"/>
      <line x1="531" y1="164" x2="761" y2="164" stroke="var(--white)" stroke-width="5"/>
    </svg>
    <ul class="contacts">
      <li>
        <span class="icon">
          <svg width="13" height="13" viewBox="0 0 24 24"><path fill="#fff" d="M6.6 10.8a15 15 0 0 0 6.6 6.6l2.2-2.2a1 1 0 0 1 1-.25 11.4 11.4 0 0 0 3.6.6 1 1 0 0 1 1 1V20a1 1 0 0 1-1 1A17 17 0 0 1 3 4a1 1 0 0 1 1-1h3.5a1 1 0 0 1 1 1c0 1.25.2 2.45.6 3.6a1 1 0 0 1-.25 1z"/></svg>
        </span>0491570156
      </li>
      <li>
        <span class="icon">
          <svg width="12" height="10" viewBox="0 0 24 18"><rect x="1" y="1" width="22" height="16" fill="none" stroke="#fff" stroke-width="2.5"/><path d="M1 1l11 9 11-9" fill="none" stroke="#fff" stroke-width="2.5"/></svg>
        </span>info@velmoracabinets.com.au
      </li>
      <li>
        <span class="icon"></span>@velmora.cabinets
      </li>
    </ul>
  </section>
</body>
</html>
```